Business Card for Graphic Design Firm

This project is for a new graphic design firm based in New Jersey called Velmoria. We outsource graphic design and marketing jobs. We want to communicate that this is a professional company but it as well creative and artistic. This card may be used as a horizontal double sided paper card or a vertical single sided translucent card so feel free to submit designs in whichever format or both.
Updates

Reason: Extending the deadline because I'm not exactly satisfied with the designs so far.

Please view the updated project brief

Target Market(s)

Adults aged 25-60

Industry/Entity Type

Graphic Design

Font styles to use
Serif
Sans Serif

Requirements
Nice to have
• Maybe a triangular pattern around the edges similar to our logo

```html
<!DOCTYPE html>
<html lang="en">
<head>
<meta charset="utf-8">
<title>Velmoria Business Card</title>
<link href="https://fonts.googleapis.com/css2?family=Caladea:wght@400;700&family=Montserrat:wght@400&display=swap" rel="stylesheet">
<style>
  :root {
    --bg: #e9e7e4;
    --card: #ffffff;
    --teal: #15708d;
    --sky: #5cc0e2;
    --orange: #f08424;
    --amber: #f8b21d;
    --grey: #6f7173;
    --ink: #1f6a85;
  }
  * { box-sizing: border-box; margin: 0; padding: 0; }
  html, body { width: 1200px; height: 873px; overflow: hidden; }
  body {
    background: var(--bg);
    font-family: "Caladea", Georgia, serif;
    position: relative;
  }
  .card {
    position: absolute;
    top: 286px;
    width: 520px;
    height: 300px;
    background: var(--card);
    box-shadow: 0 6px 18px rgba(0,0,0,.15);
    overflow: hidden;
  }
  .card--front { left: 50px; }
  .card--back { left: 630px; }

  .corner-accent {
    position: absolute;
    width: 44px;
    height: 26px;
    background: linear-gradient(90deg, var(--teal), var(--sky) 50%, var(--amber) 75%, var(--orange));
    opacity: .9;
  }
  .corner-accent--tl { top: 14px; left: 14px; }
  .corner-accent--tr { top: 14px; right: 14px; }
  .corner-accent--bl { bottom: 14px; left: 14px; }
  .corner-accent--br { bottom: 14px; right: 14px; }

  .wordmark {
    font-family: "Montserrat", Arial, sans-serif;
    font-weight: 400;
    color: var(--grey);
    letter-spacing: .12em;
    text-transform: uppercase;
    display: flex;
    align-items: center;
    gap: 10px;
  }
  .wordmark__dot {
    width: 14px; height: 14px;
    background: var(--sky);
  }

  .card--front .wordmark {
    position: absolute;
    top: 44px;
    left: 60px;
    font-size: 22px;
  }
  .identity {
    position: absolute;
    top: 90px;
    left: 60px;
  }
  .identity__name {
    color: var(--ink);
    font-size: 22px;
    font-weight: 700;
    letter-spacing: .03em;
    text-transform: uppercase;
  }
  .identity__role {
    color: var(--orange);
    font-size: 15px;
    margin-top: 2px;
  }
  .divider {
    position: absolute;
    top: 160px;
    left: 60px;
    right: 60px;
    height: 1.5px;
    background: var(--orange);
  }
  .contacts {
    position: absolute;
    top: 176px;
    left: 60px;
    right: 40px;
    display: grid;
    grid-template-columns: repeat(3, auto);
    gap: 12px 20px;
    list-style: none;
  }
  .contact {
    display: flex;
    align-items: center;
    gap: 6px;
    color: var(--ink);
    font-size: 14px;
  }
  .contact__icon {
    width: 13px; height: 13px;
    flex: none;
  }

  .brand-field {
    position: absolute;
    left: 0;
    top: 30px;
    width: 210px;
    height: 170px;
    background: linear-gradient(135deg, var(--grey) 0%, var(--sky) 35%, var(--teal) 60%, var(--amber) 78%, var(--orange) 100%);
    opacity: .85;
  }
  .card--back .wordmark {
    position: absolute;
    right: 44px;
    top: 150px;
    font-size: 28px;
  }
</style>
</head>
<body>
  <section class="card card--front" aria-label="Card front">
    <div class="corner-accent corner-accent--tl"></div>
    <div class="corner-accent corner-accent--tr"></div>
    <div class="corner-accent corner-accent--bl"></div>
    <div class="corner-accent corner-accent--br"></div>

    <div class="wordmark"><span>Velmoria</span><span class="wordmark__dot"></span></div>

    <div class="identity">
      <p class="identity__name">Daniel Hart</p>
      <p class="identity__role">Manager</p>
    </div>

    <div class="divider"></div>

    <ul class="contacts">
      <li class="contact">
        <svg class="contact__icon" viewBox="0 0 13 13"><rect width="13" height="13" rx="2" fill="#f08424"/><path d="M4 3h2l.6 2-1 .8a5 5 0 0 0 1.8 1.8l.8-1 2 .6v2c-4 .5-6.7-2.2-6.2-6.2z" fill="#fff"/></svg>
        +120 555 0142
      </li>
      <li class="contact">
        <svg class="contact__icon" viewBox="0 0 13 13"><rect width="13" height="13" rx="2" fill="#f08424"/><rect x="4" y="2.5" width="5" height="8" rx="1" fill="#fff"/></svg>
        +120 555 0187
      </li>
      <li class="contact">
        <svg class="contact__icon" viewBox="0 0 13 13"><rect width="13" height="13" rx="2" fill="#f08424"/><rect x="3" y="4" width="7" height="5" fill="#fff"/><rect x="4" y="2.5" width="5" height="1.5" fill="#fff"/></svg>
        +120 555 0199
      </li>
      <li class="contact">
        <svg class="contact__icon" viewBox="0 0 13 13"><rect width="13" height="13" rx="2" fill="#f08424"/><rect x="3" y="4" width="7" height="5" fill="#fff"/><path d="M3 4l3.5 3L10 4" stroke="#f08424" fill="none"/></svg>
        danielhart@mail.com
      </li>
      <li class="contact">
        <svg class="contact__icon" viewBox="0 0 13 13"><rect width="13" height="13" rx="2" fill="#f08424"/><circle cx="6.5" cy="6.5" r="3.5" fill="none" stroke="#fff"/><path d="M3 6.5h7M6.5 3v7" stroke="#fff"/></svg>
        www.velmoria.com
      </li>
    </ul>
  </section>

  <section class="card card--back" aria-label="Card back">
    <div class="brand-field" role="img" aria-label="Large brand mark decoration in grey, blue, teal and orange tones"></div>
    <div class="wordmark"><span>Velmoria</span><span class="wordmark__dot"></span></div>
  </section>
</body>
</html>
```